Mens Jewellery Homepage - Modern, Stylish Mens Ring Brand - Homepage

Project Overview: KestrelHoops.com is a men's accessories brand specializing in high-quality mens rings.

The objective of this redesign is to create a modern, visually appealing homepage that is easy to navigate, showcases a wide range of rings, highlights personalization options, and builds trust with customers.

The new design should make a strong impression while reflecting the brand's premium quality and commitment to craftsmanship.

The focus will be on a sleek aesthetic that aligns with the tastes of men shopping for wedding bands, engagement rings, or fashion accessories.

Objectives:

Modern and Sleek Aesthetic:

A clean, minimalist design that emphasizes high-quality product imagery and thoughtful use of space.
Contemporary color palette that conveys elegance and sophistication, with accents that highlight key elements without overwhelming the user.

Consistent and easy-to-read typography that reflects the brand’s modern and masculine identity.

Showcasing Products:
Hero Section: A image to show off 3 or 4 ring designs that could be used for weddings or fashion.

Product Highlights: Below the hero banner, showcase product categories by color (see current website for colors)

Featured Products: Display a selection of “Top Rated” or “Customer Favorites” rings to help guide users toward popular choices.

Personalization Section:
A dedicated section promoting the ability to personalize rings, emphasizing features like engraving with names, dates, or special messages.
Include lifestyle images of personalized rings to inspire customers and give them an idea of what’s possible.
Use callouts such as “Make It Yours” or “Personalize Your Ring” to encourage users to explore the customization options available for each product.

Building Trust:

A space to show 5 or 6 testimonials and other trust elements

Symbols / text to show

free delivery
free returns
every ring stock
fast delivery
customer images (from reviews)

Driving Conversions:
Include a prominent call-to-action (CTA) button in the hero section with text like “Shop Now” or “Discover Our Collections.”

User Experience:
Fast, easy-to-navigate layout with simple and intuitive categories. Product categories and main sections should be clearly visible and easy to access without overwhelming the user.
Design the homepage to feel cohesive and uncluttered, with a logical flow from product discovery to personalization and checkout.

Visual Elements and Imagery:
Use ring images from our site, but add backgrounds etc to make the image on the homepage more interesting.

Personalization Options: Use visual representations (like ring mockups) showing where personalization options (such as engravings) would appear on the product.

I like (and would like to see some different designs from our current design)
Vorm.com for design
ridgeloops.com

Target Market(s)

Men - 20 to 35

Number of Pages Required

1 page

Requirements
Must have
• Easy navigation, Trust, Modern, Clean,
Nice to have
• Would like to see Different designs like Vorm.com - RidgeLoops.com

```html
<!DOCTYPE html>
<html lang="en">
<head>
<meta charset="utf-8">
<title>Kestrel Hoops — Men's Rings</title>
<link href="https://fonts.googleapis.com/css2?family=Roboto:ital,wght@0,400;0,500;0,700;1,400&family=Tinos:wght@400;700&display=swap" rel="stylesheet">
<style>
:root{
  --teal:#1f8a8b;
  --teal-dark:#176f70;
  --ink:#1c1c1c;
  --text:#444;
  --muted:#777;
  --soft:#f3f3f3;
  --gold-soft:#f5e6b0;
  --star:#f2b01e;
  --footer:#232323;
  --white:#fff;
}
*{box-sizing:border-box;margin:0;padding:0}
html,body{width:1200px;height:3456px;overflow:hidden}
body{font-family:'Roboto',sans-serif;color:var(--ink);background:var(--white);position:relative}
.serif{font-family:'Tinos',serif}
a{color:inherit;text-decoration:none}

/* top bar */
.promo-bar{height:30px;background:#1a1a1a;color:#fff;font-size:11px;font-weight:500;display:flex;align-items:center;justify-content:center;letter-spacing:.2px}

/* nav */
.site-nav{height:62px;display:flex;align-items:center;padding:0 112px;border-bottom:1px solid #eee}
.brand{display:flex;align-items:center;gap:10px;font-weight:500;letter-spacing:4px;font-size:17px;color:var(--ink);width:220px}
.brand-dot{width:44px;height:44px;border:3px solid var(--ink);border-radius:50%}
.nav-links{display:flex;gap:40px;margin-left:8px;font-size:13px;color:#333}
.nav-links .active{color:var(--teal)}
.nav-tools{margin-left:auto;display:flex;align-items:center;gap:16px}
.nav-tools svg{width:18px;height:18px;fill:#333}
.search-btn{margin-left:18px;border:2px solid var(--teal);border-radius:20px;padding:9px 16px;font-size:13px;font-weight:700;display:flex;align-items:center;gap:6px}
.search-btn svg{width:15px;height:15px;fill:none;stroke:var(--ink);stroke-width:2.5}

/* hero */
.hero{position:relative;height:514px;background:radial-gradient(ellipse at 70% 30%,#ffffff 0%,#e6e8ec 40%,#c7cad0 100%);text-align:center}
.hero-art{position:absolute;inset:0}
.ring-blob{position:absolute;border-radius:50%;}
.hero-copy{position:absolute;left:0;right:0;top:150px}
.hero-copy .kicker{font-size:26px;letter-spacing:1px;color:#222}
.hero-copy h1{font-family:'Tinos',serif;font-weight:400;font-size:64px;letter-spacing:1px;margin-top:8px}
.btn-outline{display:inline-block;border:2px solid var(--teal);border-radius:24px;padding:11px 18px;font-size:13px;font-weight:700;background:rgba(255,255,255,.5)}
.hero .btn-outline{margin-top:20px}

/* section heads */
.section-head{display:flex;align-items:center;justify-content:space-between;padding:0 112px}
.section-title{font-family:'Tinos',serif;font-size:38px;font-weight:400;letter-spacing:.5px}
.section-title b{font-weight:700}

/* categories */
.categories{padding-top:88px}
.cat-grid{margin-top:40px;display:grid;grid-template-columns:287px 300px 300px 283px;grid-template-rows:219px 219px;column-gap:10px;row-gap:12px}
.cat{position:relative;background:var(--soft);overflow:hidden}
.cat.tall{grid-row:span 2}
.cat.featured{background:var(--gold-soft)}
.cat-label{position:absolute;left:16px;top:24px;font-size:14px;font-weight:700;color:var(--ink)}
.cat-label i{display:block;font-weight:400;color:#555;margin-top:4px;font-size:16px}
.cat.tall .cat-label{left:24px;top:auto;bottom:110px;transform:rotate(-90deg);transform-origin:left bottom;white-space:nowrap;left:40px}
.cat .btn-outline{position:absolute;left:12px;top:82px;padding:9px 20px;background:transparent}
.cat-photo{position:absolute;border-radius:50%}

/* favourites */
.favourites{padding-top:90px;position:relative}
.products{margin:38px 112px 0;display:grid;grid-template-columns:repeat(4,223px);column-gap:28px}
.product-photo{position:relative;height:274px;background:var(--soft)}
.product.hover .product-photo{background:var(--gold-soft)}
.badge{position:absolute;left:12px;top:14px;font-family:'Tinos',serif;font-size:15px;color:var(--teal)}
.product.hover .badge{color:var(--ink)}
.product-icons{position:absolute;right:12px;top:14px;display:flex;flex-direction:column;gap:10px}
.product-icons svg{width:16px;height:16px}
.ring-shot{position:absolute;left:30px;top:44px;width:170px;height:200px;border-radius:50%}
.product-name{margin-top:22px;font-size:15px;line-height:20px;color:#555}
.product.hover .product-name,.product.hover .price{color:var(--teal)}
.stars{color:var(--star);font-size:19px;letter-spacing:1px;margin-top:2px}
.price{font-size:20px;margin-top:2px}
.arrow{position:absolute;width:38px;height:38px;border-radius:50%;border:2px solid var(--teal);display:flex;align-items:center;justify-content:center;background:#fff}
.arrow.filled{background:var(--teal)}
.arrow svg{width:14px;height:14px;fill:none;stroke:var(--teal);stroke-width:2.4}
.arrow.filled svg{stroke:#fff}

/* engraving */
.engraving{position:absolute;top:1892px;left:0;width:1200px;height:504px;background:linear-gradient(90deg,#dfe1e6 0%,#eceef1 50%,#e3e6ea 100%)}
.engrave-photo{position:absolute;left:20px;top:60px;width:520px;height:400px;border-radius:46% 54% 48% 52%;background:radial-gradient(ellipse at 45% 45%,#fbe6a4 0%,#e0b24a 45%,#b9852a 80%,rgba(185,133,42,0) 100%)}
.engrave-copy{position:absolute;left:601px;top:52px;width:500px}
.engrave-copy h2{font-family:'Tinos',serif;font-weight:400;font-size:38px;line-height:44px;letter-spacing:.5px}
.engrave-copy h2 b{font-weight:700}
.engrave-copy p{font-size:15px;line-height:24px;color:#555;margin-top:28px}
.engrave-copy p + p{margin-top:8px}
.engrave-copy .btn-outline{margin-top:22px;padding:11px 18px}

/* testimonials */
.testimonials{position:absolute;top:2396px;left:0;width:1200px}
.testimonials .section-head{padding-top:88px}
.t-arrows{display:flex;gap:16px;position:relative;width:92px;height:38px}
.t-arrows .arrow{position:static}
.t-track{position:relative;height:270px;margin-top:50px;overflow:hidden}
.t-card{position:absolute;top:12px;width:236px;height:256px;background:#fff;box-shadow:0 0 8px rgba(0,0,0,.08);text-align:center;padding:70px 12px 0}
.avatar{position:absolute;left:50%;top:-10px;transform:translateX(-50%);width:74px;height:74px;border-radius:50%}
.t-name{font-size:20px;font-weight:700;color:var(--teal)}
.t-stars{color:var(--star);font-size:12px;letter-spacing:3px;margin-top:4px}
.t-text{font-style:italic;font-size:15px;line-height:26px;color:#555;margin-top:6px}

/* trust band */
.trust{position:absolute;top:2841px;left:0;width:1200px;height:179px;background:var(--teal);display:flex;padding-left:99px}
.trust-item{width:248px;text-align:center;color:#fff;padding-top:30px;border-right:1px solid rgba(255,255,255,.8);margin:20px 0 0}
.trust-item:last-child{border-right:none}
.trust-item h3{font-size:16px;font-weight:700;margin-top:-20px}
.trust-item svg{margin-top:14px;width:72px;height:64px;fill:none;stroke:#fff;stroke-width:2}

/* footer */
.footer{position:absolute;top:3020px;left:0;width:1200px;height:436px;background:var(--footer);color:#fff}
.footer-brand{position:absolute;left:112px;top:80px;display:flex;align-items:center;gap:12px;font-size:20px;font-weight:500;letter-spacing:5px}
.footer-brand .brand-dot{border-color:#fff;width:62px;height:62px;border-width:4px}
.social{position:absolute;left:150px;top:170px;display:flex;gap:15px}
.social span{width:38px;height:38px;border-radius:50%;border:1.5px solid #fff}
.social span:first-child{background:#fff}
.f-col{position:absolute;top:74px}
.f-col h4{font-size:19px;font-weight:500;margin-bottom:22px}
.f-col li{list-style:none;font-size:15px;line-height:31px}
.f-col.links{left:417px}
.f-col.important{left:608px}
.f-col.contact{left:855px}
.contact-row{display:flex;gap:22px;align-items:flex-start;margin-bottom:28px}
.contact-row svg{width:20px;height:20px;fill:#fff;margin-top:12px;flex:none}
.contact-row b{display:block;font-weight:500;font-size:16px}
.contact-row span{font-size:15px;line-height:20px}
.payments{position:absolute;top:3385px;left:0;width:1200px;display:flex;justify-content:center;gap:8px}
.payments span{width:32px;height:20px;border-radius:3px;background:#e8e8e8}
.payments span:nth-child(odd){background:#c9d3e6}
.copyright{position:absolute;top:3418px;left:0;width:1200px;text-align:center;color:#fff;font-size:15px}
</style>
</head>
<body>

<div class="promo-bar">ENGRAVING THE RINGS&nbsp; WITH NAMES, DATES, OR SPECIAL MESSAGES</div>

<nav class="site-nav">
  <a class="brand" href="#"><span class="brand-dot"></span>KESTREL HOOPS</a>
  <div class="nav-links">
    <a class="active" href="#">TRY AT HOME</a>
    <a href="#">SHOP BY MATERIA</a>
    <a href="#">SHOP BY COLOR</a>
  </div>
  <div class="nav-tools">
    <svg viewBox="0 0 24 24"><circle cx="12" cy="7" r="5"/><path d="M2 23c0-6 4.5-9 10-9s10 3 10 9z"/></svg>
    <svg viewBox="0 0 24 24"><path d="M12 22 3 13C0 10 1 4 6 3.5c3-.3 5 2 6 3.5 1-1.5 3-3.8 6-3.5 5 .5 6 6.5 3 9.5z"/></svg>
    <svg viewBox="0 0 24 24"><path d="M3 8h18l-1.5 14h-15z"/><path d="M8 8V6a4 4 0 0 1 8 0v2" fill="none" stroke="#333" stroke-width="2"/></svg>
    <a class="search-btn" href="#"><svg viewBox="0 0 24 24"><circle cx="10" cy="10" r="7"/><path d="m15 15 6 6"/></svg>SEARCH</a>
  </div>
</nav>

<header class="hero">
  <div class="hero-art" role="img" aria-label="Gold, two-tone and diamond rings resting on sparkling silver glitter">
    <div class="ring-blob" style="left:230px;top:20px;width:220px;height:150px;background:radial-gradient(ellipse,#e7b86c 0%,rgba(205,140,60,.35) 60%,rgba(0,0,0,0) 72%)"></div>
    <div class="ring-blob" style="left:810px;top:30px;width:260px;height:200px;background:radial-gradient(ellipse,#e9c08a 0%,rgba(200,160,110,.35) 60%,rgba(0,0,0,0) 72%)"></div>
    <div class="ring-blob" style="left:105px;top:280px;width:300px;height:180px;background:radial-gradient(ellipse,#eec572 0%,rgba(210,160,70,.4) 60%,rgba(0,0,0,0) 72%)"></div>
    <div class="ring-blob" style="left:700px;top:270px;width:240px;height:200px;background:radial-gradient(ellipse,#e8cf7a 0%,rgba(190,190,190,.4) 60%,rgba(0,0,0,0) 72%)"></div>
  </div>
  <div class="hero-copy">
    <div class="kicker">WELCOME TO</div>
    <h1>KESTREL HOOPS</h1>
    <a class="btn-outline" href="#">SHOP NOW</a>
  </div>
</header>

<section class="categories">
  <div class="section-head">
    <h2 class="section-title"><b>PRODUCT</b> CATEGORIES</h2>
    <a class="btn-outline" href="#">VIEW MORE</a>
  </div>
  <div class="cat-grid">
    <div class="cat tall">
      <div class="cat-label">STRONG FEARLESS MAJESTIC<i>Black Collection</i></div>
      <div class="cat-photo" role="img" aria-label="Two black tungsten rings" style="left:70px;top:50px;width:200px;height:330px;background:radial-gradient(ellipse,#2a2a2a 0%,#555 50%,rgba(243,243,243,0) 72%)"></div>
    </div>
    <div class="cat">
      <div class="cat-label">CALM SOPHISTICATED ELEGANT<i>Silver Collection</i></div>
      <div class="cat-photo" role="img" aria-label="Silver and black tungsten rings" style="left:120px;top:40px;width:170px;height:170px;background:radial-gradient(ellipse,#c9c9c9 0%,#888 45%,rgba(243,243,243,0) 72%)"></div>
    </div>
    <div class="cat featured">
      <div class="cat-label">CONSTANT LOYAL TRUE<i>Blue Collection</i></div>
      <a class="btn-outline" href="#">SHOP NOW</a>
      <div class="cat-photo" role="img" aria-label="Black rings with blue inlay" style="left:120px;top:30px;width:180px;height:180px;background:radial-gradient(ellipse,#1b47a8 0%,#223 45%,rgba(245,230,176,0) 72%)"></div>
    </div>
    <div class="cat tall">
      <div class="cat-label">ROMANTIC VINTAGE SUBLIME<i>Rose Gold Collection</i></div>
      <div class="cat-photo" role="img" aria-label="Rose gold and brushed silver rings" style="left:70px;top:40px;width:200px;height:350px;background:radial-gradient(ellipse,#d99a7a 0%,#999 50%,rgba(243,243,243,0) 72%)"></div>
    </div>
    <div class="cat">
      <div class="cat-label">BRIGHT BRILLIANT CLASSIC<i>Gold &nbsp;Collection</i></div>
      <div class="cat-photo" role="img" aria-label="Pair of gold wedding bands" style="left:60px;top:50px;width:230px;height:170px;background:radial-gradient(ellipse,#f0c35c 0%,#cf9a2c 40%,rgba(243,243,243,0) 72%)"></div>
    </div>
    <div class="cat">
      <div class="cat-label">AUTHENTIC GENUINE SIMPLE<i>Brown Collection</i></div>
      <div class="cat-photo" role="img" aria-label="Rings with wood inlay" style="left:80px;top:40px;width:210px;height:180px;background:radial-gradient(ellipse,#8a3f22 0%,#333 45%,rgba(243,243,243,0) 72%)"></div>
    </div>
  </div>
</section>

<section class="favourites">
  <div class="section-head"><h2 class="section-title"><b>CUSTOMER</b> FAVORITES</h2></div>
  <div class="products">
    <article class="product">
      <div class="product-photo"><span class="badge">18% OFF</span>
        <div class="ring-shot" role="img" aria-label="Black titanium ring with blue inner band" style="background:radial-gradient(ellipse,#1d4fb0 0%,#1a1a1a 48%,rgba(243,243,243,0) 72%)"></div></div>
      <div class="product-name">Steadfast – Men's Titanium Ring – Black and Blue Gent's Band 6mm or 8mm</div>
      <div class="stars">★★★★★</div><div class="price">£45.00</div>
    </article>
    <article class="product hover">
      <div class="product-photo"><span class="badge">18% OFF</span>
        <div class="product-icons">
          <svg viewBox="0 0 24 24"><path d="M12 21 4 13C1 10 2 5 6.5 4.5c2.5-.2 4.5 1.5 5.5 3 1-1.5 3-3.2 5.5-3C22 5 23 10 20 13z" fill="none" stroke="#555" stroke-width="2"/></svg>
          <svg viewBox="0 0 24 24"><path d="M4 9h16l-1.5 12h-13z" fill="#555"/><path d="M8 9V7a4 4 0 0 1 8 0v2" fill="none" stroke="#555" stroke-width="2"/></svg>
        </div>
        <div class="ring-shot" role="img" aria-label="Matte black tungsten ring" style="background:radial-gradient(ellipse,#3a3a3a 0%,#111 48%,rgba(245,230,176,0) 72%)"></div></div>
      <div class="product-name">Nightfall – Men's Tungsten Ring Black Band for Him 6mm or 8mm</div>
      <div class="stars">★★★★★</div><div class="price">£44.00</div>
    </article>
    <article class="product">
      <div class="product-photo"><span class="badge">18% OFF</span>
        <div class="ring-shot" role="img" aria-label="Brushed silver ring with black interior" style="background:radial-gradient(ellipse,#bdbdbd 0%,#555 50%,rgba(243,243,243,0) 72%)"></div></div>
      <div class="product-name">Pathfinder – Men's Tungsten Ring Silver and Black Gent's Band 8mm</div>
      <div class="stars">★★★★★</div><div class="price">£56.00</div>
    </article>
    <article class="product">
      <div class="product-photo"><span class="badge">18% OFF</span>
        <div class="ring-shot" role="img" aria-label="Black ring with wood inner sleeve" style="background:radial-gradient(ellipse,#9b3a1e 0%,#222 48%,rgba(243,243,243,0) 72%)"></div></div>
      <div class="product-name">Wanderer – Men's Tungsten Ring Black and Wood Band for Him 8mm</div>
      <div class="stars">★★★★★</div><div class="price">£54.99</div>
    </article>
  </div>
  <a class="arrow" href="#" style="left:32px;top:1522px;position:absolute" aria-label="Previous"><svg viewBox="0 0 14 14"><path d="M9 2 4 7l5 5"/></svg></a>
  <a class="arrow filled" href="#" style="left:1117px;top:1522px;position:absolute" aria-label="Next"><svg viewBox="0 0 14 14"><path d="m5 2 5 5-5 5"/></svg></a>
</section>

<section class="engraving">
  <div class="engrave-photo" role="img" aria-label="Two gold wedding bands with an engraved message inside"></div>
  <div class="engrave-copy">
    <h2><b>ENGRAVING THE RINGS</b><br>WITH NAMES, DATES, OR<br>SPECIAL MESSAGES</h2>
    <p>Lorem ipsum dolor sit amet, consectetur adipiscing lit, sed do eiusmod tempor incididunt ut labore et dolore magna aliqua. Quis ipsum endisse ltrices gravida. Risus commodo viverra maecenas ccumsan lacus vel facilisistrices gravida Risus commodo.</p>
    <p>Lorem ipsum dolor sit amet, consectetur adipiscing lit, sed do eiusmod tempor incididunt ut labore et dolore magna aliqua.</p>
    <a class="btn-outline" href="#">PERSONALIZE YOUR RING</a>
  </div>
</section>

<section class="testimonials">
  <div class="section-head">
    <h2 class="section-title"><b>CLIENT</b> TESTIMONIALS</h2>
    <div class="t-arrows">
      <a class="arrow" href="#" aria-label="Previous"><svg viewBox="0 0 14 14"><path d="M9 2 4 7l5 5"/></svg></a>
      <a class="arrow filled" href="#" aria-label="Next"><svg viewBox="0 0 14 14"><path d="m5 2 5 5-5 5"/></svg></a>
    </div>
  </div>
  <div class="t-track">
    <div class="t-card" style="left:0"><div class="avatar" role="img" aria-label="Customer portrait" style="background:#8c7466"></div>
      <div class="t-name">HATTIE</div><div class="t-stars">★★★★★</div>
      <p class="t-text">Super service, thank you so much. The ring fits perfectly and looks great. My boyfriend is very happy</p></div>
    <div class="t-card" style="left:255px"><div class="avatar" role="img" aria-label="Customer portrait" style="background:#a08a78"></div>
      <div class="t-name">GORDON</div><div class="t-stars">★★★★★</div>
      <p class="t-text">Thank you so much for exchanging the ring and for doing it so quickly. I'm delighted.</p></div>
    <div class="t-card" style="left:510px"><div class="avatar" role="img" aria-label="Customer portrait" style="background:#6f6a68"></div>
      <div class="t-name">OWEN MARSH</div><div class="t-stars">★★★★★</div>
      <p class="t-text">Orbit - Men's Silicone Ring - Black Domed Band for Him Amazing product and service</p></div>
    <div class="t-card" style="left:765px"><div class="avatar" role="img" aria-label="Customer portrait" style="background:#c98a58"></div>
      <div class="t-name">DANIEL FAIRLEY</div><div class="t-stars">★★★★★</div>
      <p class="t-text">The Victor - Men's Tungsten Ring - Silver Black Gold Band for Him 6mm or 8mm Strong and sturdy brilliant quality</p></div>
    <div class="t-card" style="left:1020px"><div class="avatar" role="img" aria-label="Customer portrait" style="background:#7a5c4c"></div>
      <div class="t-name">PRIYA SEN</div><div class="t-stars">★★★★★</div>
      <p class="t-text">Personalised Ring Engraving Beautifully engraved, very clean finish. Very professional service.</p></div>
  </div>
</section>

<section class="trust">
  <div class="trust-item"><h3>FREE DELIVERY</h3>
    <svg viewBox="0 0 72 64"><path d="M6 22h40v28H6zM46 32h12l8 10v8H46"/><circle cx="18" cy="52" r="5"/><circle cx="56" cy="52" r="5"/><path d="M20 22c-4-8 6-12 8-4 2-8 12-4 8 4"/><text x="12" y="40" fill="#fff" stroke="none" font-size="11" font-family="Roboto" font-weight="700">FREE</text></svg></div>
  <div class="trust-item"><h3>FREE RETURNS</h3>
    <svg viewBox="0 0 72 64"><path d="M22 14 44 4l20 10v26L44 52 22 40zM22 14l22 12 20-12M44 26v26"/><path d="M14 42a10 10 0 1 0 10 12M14 42l-2 6 6 0"/></svg></div>
  <div class="trust-item"><h3>FAST DELIVERY</h3>
    <svg viewBox="0 0 72 64"><path d="M14 24h32v24H14zM46 32h12l8 10v6H46"/><circle cx="22" cy="50" r="5"/><circle cx="56" cy="50" r="5"/><circle cx="18" cy="16" r="10"/><path d="M18 10v6l4 3M2 36h10M4 42h8"/></svg></div>
  <div class="trust-item"><h3>EVERY RING STOCK</h3>
    <svg viewBox="0 0 72 64"><circle cx="36" cy="42" r="18"/><circle cx="36" cy="42" r="12"/><path d="M28 24l-4-10h24l-4 10zM24 14l12 10 12-10"/></svg></div>
</section>

<footer class="footer">
  <div class="footer-brand"><span class="brand-dot"></span>KESTREL HOOPS</div>
  <div class="social" aria-label="Social links"><span></span><span></span><span></span></div>
  <div class="f-col links"><h4>QUICK LINKS</h4><ul>
    <li>TRY AT HOME</li><li>SHOP BY MATERIA</li><li>SHOP BY COLOR</li><li>FREE RING SIZER</li><li>RING ENGRAVING</li><li>FREE DELIVERY</li><li>RETURNS</li></ul></div>
  <div class="f-col important"><h4>IMPORTANT LINKS</h4><ul style="line-height:36px">
    <li style="line-height:36px">CONTACT US</li><li style="line-height:36px">SIZE GUIDE</li><li style="line-height:36px">SHIPPING POLICY</li><li style="line-height:36px">RETURN &amp; REFUND POLICY</li><li style="line-height:36px">TERMS OF SERVICE</li><li style="line-height:36px">PRIVACY POLICY</li></ul></div>
  <div class="f-col contact"><h4>CONTACT</h4>
    <div class="contact-row"><svg viewBox="0 0 24 24"><path d="M2 5h20v14H2z"/><path d="m2 5 10 8 10-8" fill="none" stroke="#232323" stroke-width="2"/></svg><div><b>EMAIL:</b><span>hello@kestrelhoops.com</span></div></div>
    <div class="contact-row"><svg viewBox="0 0 24 24"><path d="M6 2 10 7 7.5 9.5c1.5 3 4 5.5 7 7L17 14l5 4-2.5 3.5C10 21 3 14 2.5 4.5z"/></svg><div><b>PHONE NO:</b><span>01632 960418</span></div></div>
    <div class="contact-row"><svg viewBox="0 0 24 24"><path d="M12 23S4 14 4 9a8 8 0 0 1 16 0c0 5-8 14-8 14z"/><circle cx="12" cy="9" r="3" fill="#232323"/></svg><div><b>ADDRESS</b><span>Lorem ipsum dolor sit<br>nsectetur adipiscing,USA</span></div></div>
  </div>
</footer>
<div class="payments" aria-label="Accepted payment methods"><span></span><span></span><span></span><span></span><span></span><span></span><span></span><span></span></div>
<div class="copyright">Copyright © 2024 Kestrel Hoops | all rights reserved.</div>

</body>
</html>
```